Small legal and financial translation company needs Squarespace website, brochure and logo

Hello,
We are Lumarin Services (www.lumarinservices-example.com), a boutique legal and financial translation company. We offer our services mainly to Spanish customers. Our primary line of business is the translation of financial statements, but we translate a wide variety legal and financial texts.
The project we are offering comprises three parts: a redo of the current website, an informational brochure for potential customer and a logo design. These three parts should provide a consistent image. We would develop content soon.
We are looking for a website that would look like a typical law firm website, nothing too fancy. Right now, it is in English, Spanish and French, although the new site need only be in English and Spanish. There must be good toggling between the English and Spanish versions. There would be no need for tie-ins to social media and it would not contain a blog. Basically, a static site. We aren't interesting in driving traffic to the site or SEO, as we will contact nearly all potential customers beforehand. The website must be built in Squarespace to enable a smooth transition. The content would be similar to the current page, we'll be working on the exact content, but a rough draft is attached.
The brochure will be some three pages and would introduce the company to potential customers, using similar images as the website and the logo to be designed.
The only specifications for the logo is, as the website and brochure, it convey a sense of security and trust.
Feel free to ask with any questions as this is the first time we have used this platform.
Thank you!
Updates

I've added a more or less final version for the text in the brochure and updated the brief. Added Wednesday, June 10, 2015

Target Market(s)

Spanish law firms, auditors, accountants, banks, investment firms

Industry/Entity Type

Finance

Logo Text

Lumarin Services

Number of Pages Required

5+ page

Font styles to use
Serif

Requirements
Must have
• The website must be built in Squarespace and have a good option to toggle between English and Spanish versions.
• Brochure must be in both English and Spanish, I'm attaching a rough draft of the information that it will probably have. This should give an idea about what to include and the spacing. I will update it to include the final information.
Nice to have
• Would be nice to have some quality finance- and legal-related images
Should not have
• Vibrant colours

```html
<!DOCTYPE html>
<html lang="en">
<head>
<meta charset="utf-8">
<title>Lumarin Services – Who Are We?</title>
<link rel="stylesheet" href="https://fonts.googleapis.com/css2?family=Cinzel:wght@400&family=Crimson+Text:wght@400;700&family=Open+Sans:wght@400&display=swap">
<style>
  :root {
    --backdrop: #cbcbcb;
    --paper: #ffffff;
    --navy: #27417e;
    --ink: #111111;
    --text: #2a2a2a;
    --label: #3a3a3a;
    --photo-light: #b9b9b9;
    --photo-dark: #3c3c3c;
  }
  * { box-sizing: border-box; margin: 0; padding: 0; }
  html, body {
    width: 1200px; height: 1200px; overflow: hidden;
    background: var(--backdrop);
  }
  .stage { position: relative; width: 1200px; height: 1200px; }
  .page-label {
    position: absolute; top: 36px; left: 0; width: 1240px;
    text-align: center;
    font: 400 35px/1 "Open Sans", sans-serif;
    color: var(--label);
  }
  .page {
    position: absolute; left: 268px; top: 110px;
    width: 699px; height: 991px;
    background: var(--paper);
    box-shadow: 0 4px 14px rgba(0,0,0,0.35);
    overflow: hidden;
  }
  .page-art { position: absolute; inset: 0; }
  .intro {
    position: absolute; left: 45px; top: 536px; width: 614px;
    color: var(--text);
    font-family: "Crimson Text", serif;
  }
  .intro-title {
    font: 400 31px/1 "Cinzel", serif;
    color: var(--navy);
    letter-spacing: 0.5px;
    margin-bottom: 22px;
  }
  .intro-body {
    font-size: 13.6px; line-height: 19.5px;
    text-align: justify; letter-spacing: -0.2px;
  }
  .highlights { list-style: none; margin-top: 35px; }
  .highlight {
    display: flex; align-items: center; gap: 8px;
    font-size: 13.8px; line-height: 1; margin-bottom: 17.5px;
    letter-spacing: -0.2px;
  }
  .highlight strong { color: var(--ink); font-weight: 700; }
  .tick { width: 16px; height: 16px; flex: none; margin-left: 5px; }
  .footer-url {
    position: absolute; left: 24px; top: 953px;
    font: 400 18.5px/1 "Crimson Text", serif;
    color: var(--paper);
  }
</style>
</head>
<body>
<main class="stage">
  <p class="page-label">Page 2</p>

  <article class="page">
    <svg class="page-art" width="699" height="991" viewBox="0 0 699 991">
      <defs>
        <linearGradient id="photoTone" x1="0" y1="0" x2="0.4" y2="1">
          <stop offset="0" stop-color="var(--photo-light)"/>
          <stop offset="1" stop-color="var(--photo-dark)"/>
        </linearGradient>
      </defs>
      <rect class="hero-photo" x="0" y="0" width="699" height="460" fill="url(#photoTone)"
            role="img" aria-label="Black and white photograph of a team of four business professionals in suits standing in an office"/>
      <!-- header shapes -->
      <polygon points="0,477 617,450 699,445 699,991 0,991" fill="var(--paper)"/>
      <polygon points="362,412 699,365 699,445 617,450" fill="var(--ink)"/>
      <polygon points="558,384 658,325 658,370" fill="var(--navy)"/>
      <polygon points="0,363 602,450 0,477" fill="var(--navy)"/>
      <line x1="0" y1="362" x2="617" y2="449" stroke="var(--paper)" stroke-width="3"/>
      <!-- footer shapes -->
      <polygon points="362,956 699,923 699,991" fill="var(--ink)"/>
      <polygon points="534,937 662,880 674,924" fill="var(--navy)"/>
      <polygon points="0,923 699,991 0,991" fill="var(--navy)"/>
    </svg>

    <section class="intro">
      <h1 class="intro-title">Who Are We?</h1>
      <p class="intro-body">We are a small, highly qualified group of professionals with backgrounds in law, financial services and translation that boasts experience in global consulting and auditing firms, law firms and companies from a wide cross-section of industries. Sensitive to the workings of the world of finance, accounting and law, we are detail-oriented experts striving to facilitate understanding among investors, companies and international organisations:</p>
      <ul class="highlights">
        <li class="highlight">
          <svg class="tick" viewBox="0 0 16 16" aria-hidden="true"><path d="M13.6 6.4A6 6 0 1 1 10.5 2.6" fill="none" stroke="var(--ink)" stroke-width="1.8"/><path d="M4.8 7.6l2.6 2.6 6.4-6.6" fill="none" stroke="var(--ink)" stroke-width="1.8"/></svg>
          <span>over <strong>30 years</strong> of combined experience</span>
        </li>
        <li class="highlight">
          <svg class="tick" viewBox="0 0 16 16" aria-hidden="true"><path d="M13.6 6.4A6 6 0 1 1 10.5 2.6" fill="none" stroke="var(--ink)" stroke-width="1.8"/><path d="M4.8 7.6l2.6 2.6 6.4-6.6" fill="none" stroke="var(--ink)" stroke-width="1.8"/></svg>
          <span>over <strong>1 million</strong> words translated annually</span>
        </li>
        <li class="highlight">
          <svg class="tick" viewBox="0 0 16 16" aria-hidden="true"><path d="M13.6 6.4A6 6 0 1 1 10.5 2.6" fill="none" stroke="var(--ink)" stroke-width="1.8"/><path d="M4.8 7.6l2.6 2.6 6.4-6.6" fill="none" stroke="var(--ink)" stroke-width="1.8"/></svg>
          <span>serving <strong>Big 4 firms</strong>, leading <strong>international law firms and banks and SELECT 30 listings and blue chips</strong></span>
        </li>
      </ul>
    </section>

    <p class="footer-url">www.lumarinservices-example.com</p>
  </article>
</main>
</body>
</html>
```